Cover Art Design for a Notebook

We are going to give away some note books to our marketing department and want an elegant art design for the cover. There is a theme centered around ABCD of marketing that we want to leverage in the design. So these letters should be prominent in the design. The ABCD stand for Agility, Boost, Customer, Data.

If you could Cleverly incorporate these words into the letters with a good design that would be good.

But please make the ABCD the focus of the artwork. The words associated with them should be subtle, in the background, visible but not the focus.

We are looking for stylish. We want people to feel proud of the ELEGANT DESIGN when they take out this notebook for business.

Also worth mentioning- We are a biotechnology company so if you incorporate elements in that theme in, on, or around the ABCD letters, it could be a good idea. As long as it doesn’t kill the rest of the design.

I will upload our logo for Kelvara Biolume Sciences later (you can see it online) and this will need to go in one corner.

Notebook will be A5 format. Image on front cover only. Need ASAP.

(Do not make baby blocks as we don’t want something that looks like a kids book)

Target Market(s)

business people who feel proud to pull out this notebook

Industry/Entity Type

Biotechnology

Colors
ec1f27
ffffff
000000

Requirements
Must have
• ELEGANT ART DESIGN USING ABCD
Nice to have
• see brief above
Should not have
• baby blocks

```html
<!DOCTYPE html>
<html lang="en">
<head>
<meta charset="utf-8">
<title>ABCD of Marketing – Notebook Cover</title>
<link rel="stylesheet" href="https://fonts.googleapis.com/css2?family=League+Spartan:wght@700;900&display=swap">
<style>
  :root {
    --cover-red: #ee2a37;
    --letter-black: #000000;
    --word-grey: #434343;
    --logo-white: #ffffff;
    --network-pink: #ff8fa8;
  }
  html, body {
    margin: 0;
    padding: 0;
    overflow: hidden;
    background: var(--cover-red);
  }
  .cover {
    position: relative;
    width: 849px;
    height: 1200px;
    background: var(--cover-red);
    overflow: hidden;
    font-family: "League Spartan", "Montserrat", sans-serif;
  }
  .network-field {
    position: absolute;
    left: 70px;
    top: 310px;
    width: 730px;
    height: 690px;
  }
  .monogram {
    position: absolute;
    left: 0;
    top: 0;
  }
  .letter { fill: var(--letter-black); }
  .letter-c-ring {
    fill: none;
    stroke: var(--letter-black);
    stroke-width: 62;
  }
  .keyword {
    font-family: "League Spartan", "Montserrat", sans-serif;
    font-weight: 700;
    font-size: 23px;
    letter-spacing: 1px;
    fill: var(--word-grey);
  }
  .brand {
    position: absolute;
    right: 86px;
    top: 1088px;
    margin: 0;
    text-align: right;
    font-weight: 700;
    font-size: 25px;
    line-height: 1.1;
    color: var(--logo-white);
  }
</style>
</head>
<body>
  <main class="cover">
    <svg class="network-field" viewBox="0 0 730 690" role="img" aria-label="Molecular network of connected nodes and lines spreading around the letters">
      <defs>
        <radialGradient id="network-glow" cx="60%" cy="55%" r="55%">
          <stop offset="0%" stop-color="#ff8fa8" stop-opacity="0.3"/>
          <stop offset="100%" stop-color="#ff8fa8" stop-opacity="0"/>
        </radialGradient>
      </defs>
      <rect width="730" height="690" fill="url(#network-glow)"/>
    </svg>

    <svg class="monogram" width="849" height="1200" viewBox="0 0 849 1200" role="img" aria-label="A B C D — Agility, Boost, Customer, Data">
      <!-- A -->
      <path class="letter letter-a" d="M 404 143 L 441 143 Q 449 143 452 151 L 515 333 L 468 333 Q 462 333 460 326 L 455 305 Q 423 292 391 305 L 386 326 Q 384 333 378 333 L 333 333 L 394 151 Q 397 143 404 143 Z"/>
      <!-- B -->
      <path class="letter letter-b" d="M 347 352 L 440 352 C 490 352 508 375 508 405 C 508 430 497 445 482 455 C 505 465 515 485 515 505 C 515 540 490 555 445 555 L 347 555 Z"/>
      <!-- C -->
      <path class="letter-c-ring" d="M 467.5 630.1 A 62 62 0 1 0 467.5 709.9"/>
      <!-- D -->
      <path class="letter letter-d" d="M 353 783 L 420 783 C 482 783 517 822 517 879 C 517 938 482 975 420 975 L 353 975 Z"/>

      <text class="keyword" transform="translate(433 222) rotate(-90)" text-anchor="middle">AGILITY</text>
      <text class="keyword" x="417" y="455" text-anchor="middle">BOOST</text>
      <path id="customer-curve" d="M 405.5 724.1 A 56 56 0 0 1 405.5 615.9" fill="none"/>
      <text class="keyword" font-size="21"><textPath href="#customer-curve" startOffset="50%" text-anchor="middle">CUSTOMER</textPath></text>
      <text class="keyword" x="421" y="888" text-anchor="middle">DATA</text>
    </svg>

    <p class="brand">Kelvara Biolume<br>Sciences</p>
  </main>
</body>
</html>
```